Kelvaro.ch is looking for business card letterhead and envelope C5 with WOW effect

We need a strong business card for our company Kelvaro.ch, logo is available. You want a black or dark background on which the logo Stark r% 26 # 252; appears. Letterhead and envelope in C5 format should be in a similar design, but does not have to be We need a strong business card for our company Kelvaro.ch, logo is available. A black or dark background is desired, on which the logo Stark comes across. The letterhead and the envelope in C5 format should have a similar design.

Target Market(s)

Private customers as well as entrepreneurs

Contact Information for Business Card

E-mail: info@kelvaro-example.ch
Web.www.Kelvaro-example.ch
Tel: +41 ( 0 ) 79 482 6037
Adresse:
Lindenweg 14
9406 Tarnbach

Hier kann man Icons verwenden für Email,Tel und Adressse

Font styles to use
Other font styles liked:
• Dubai,bold

Colors

Designer to choose colors to be used in the design.

Requirements
Must have
• WOW effect
Nice to have
• R% 26 # 252; back business card with our service listings. - VEHICLE LABELING - SHOP WINDOW LABELING - STICKERS AND MUCH MORE ... in red color

```html
<!DOCTYPE html>
<html lang="de">
<head>
<meta charset="utf-8">
<title>Kelvaro.ch – Visitenkarte</title>
<link rel="stylesheet" href="https://fonts.googleapis.com/css2?family=Saira:wght@700&family=Open+Sans:wght@400;600&display=swap">
<style>
  :root {
    --ink: #1f1c1d;
    --honey: #f2c118;
    --paper: #ffffff;
    --stage: #e4e1dc;
    --text-dark: #222222;
  }
  * { box-sizing: border-box; margin: 0; padding: 0; }
  html, body { width: 1200px; height: 843px; overflow: hidden; }
  body {
    background: var(--stage);
    font-family: "Open Sans", Arial, sans-serif;
    display: flex;
    align-items: center;
    justify-content: center;
    gap: 48px;
  }
  .card {
    position: relative;
    width: 540px;
    height: 318px;
    overflow: hidden;
    box-shadow: 0 10px 24px rgba(0,0,0,.18);
  }

  /* Front */
  .card--front { background: var(--ink); }
  .card--front .pattern {
    position: absolute;
    left: 0; top: 0;
    width: 100%; height: 100%;
  }
  .card--front .brand {
    position: absolute;
    right: 36px; top: 34px;
    text-align: right;
  }
  .brand-name {
    font-family: "Saira", Arial, sans-serif;
    font-weight: 700;
    font-size: 38px;
    line-height: 1;
    letter-spacing: 1px;
    text-transform: uppercase;
  }
  .card--front .brand-name { color: var(--honey); }
  .card--front .brand-web {
    margin-top: 6px;
    color: var(--honey);
    font-weight: 600;
    font-size: 12px;
    letter-spacing: 3.5px;
  }

  /* Back */
  .card--back { background: var(--paper); color: var(--text-dark); }
  .accent-bar {
    position: absolute;
    left: 0; top: 26px;
    width: 10px; height: 76px;
    background: var(--honey);
  }
  .accent-bar--low {
    top: auto; bottom: 30px;
    height: 22px;
    background: var(--ink);
  }
  .contact-list {
    position: absolute;
    left: 36px; top: 24px;
    list-style: none;
    font-size: 12.5px;
    line-height: 1.55;
  }
  .contact-list li, .address {
    display: flex;
    align-items: center;
    gap: 10px;
  }
  .icon { width: 14px; height: 14px; flex: none; }
  .card--back .brand {
    position: absolute;
    left: 150px; top: 138px;
    display: flex;
    align-items: center;
    gap: 14px;
  }
  .brand-mark {
    width: 26px; height: 26px;
    border-radius: 50%;
    background: var(--honey);
  }
  .card--back .brand-name { color: var(--ink); font-size: 34px; }
  .address {
    position: absolute;
    left: 36px; bottom: 26px;
    font-size: 12.5px;
    font-weight: 600;
    line-height: 1.3;
  }
</style>
</head>
<body>

  <section class="card card--front">
    <svg class="pattern" viewBox="0 0 540 318" role="img" aria-label="Yellow honeycomb pattern spreading from the left and bottom edges">
      <defs>
        <linearGradient id="honeyFade" x1="0" y1="1" x2="1" y2="0">
          <stop offset="0" stop-color="#f2c118"/>
          <stop offset="1" stop-color="#d9a910"/>
        </linearGradient>
      </defs>
      <polygon points="0,90 120,70 200,150 370,170 390,250 300,318 0,318" fill="url(#honeyFade)"/>
    </svg>
    <div class="brand">
      <div class="brand-name">Kelvaro.ch</div>
      <div class="brand-web">www.Kelvaro-example.ch</div>
    </div>
  </section>

  <section class="card card--back">
    <span class="accent-bar"></span>
    <ul class="contact-list">
      <li>
        <svg class="icon" viewBox="0 0 24 24" fill="none" stroke="#f2c118" stroke-width="2"><path d="M5 3h4l2 5-2.5 1.5a11 11 0 0 0 6 6L16 13l5 2v4a2 2 0 0 1-2 2A17 17 0 0 1 3 5a2 2 0 0 1 2-2z"/></svg>
        +41 ( 0 ) 79 482 6037
      </li>
      <li>
        <svg class="icon" viewBox="0 0 24 24" fill="none" stroke="#f2c118" stroke-width="2"><rect x="3" y="5" width="18" height="14"/><path d="M3 5l9 8 9-8"/></svg>
        info@kelvaro-example.ch
      </li>
      <li>
        <svg class="icon" viewBox="0 0 24 24" fill="none" stroke="#f2c118" stroke-width="2"><circle cx="12" cy="12" r="9"/><path d="M3 12h18M12 3c3 3 3 15 0 18M12 3c-3 3-3 15 0 18"/></svg>
        www.Kelvaro-example.ch
      </li>
    </ul>

    <div class="brand">
      <span class="brand-mark"></span>
      <span class="brand-name">Kelvaro.ch</span>
    </div>

    <span class="accent-bar accent-bar--low"></span>
    <div class="address">
      <svg class="icon" viewBox="0 0 24 24" fill="none" stroke="#f2c118" stroke-width="2"><path d="M12 22s7-7 7-12a7 7 0 0 0-14 0c0 5 7 12 7 12z"/><circle cx="12" cy="10" r="2.5"/></svg>
      <div>Lindenweg 14<br>9406 Tarnbach</div>
    </div>
  </section>

</body>
</html>
```